Web Design For Manufacturing And Outsourcing Company

Pick up the pieces from our previous developer and help us complete our website.

5 pages - Home,Machining,Sourcing,About Us, and Contact

Attached you will find screen shots of previous direction but we're open to new ideas.

We can provide all text and images needed.

Thanks!

Number of Pages Required

5+ page

```html
<!DOCTYPE html>
<html lang="en">
<head>
<meta charset="utf-8">
<title>Keel Industries</title>
<link rel="stylesheet" href="https://fonts.googleapis.com/css2?family=Montserrat:wght@400;500;600;700&family=Open+Sans:wght@400;600&display=swap">
<style>
:root{
  --ink:#222222;
  --dark:#1f1f1f;
  --orange:#e8501c;
  --orange-soft:rgba(232,80,28,.15);
  --grey:#e9e9e9;
  --white:#ffffff;
  --text:#2b2b2b;
  --field-line:#d8d8d8;
}
*{box-sizing:border-box;margin:0;padding:0}
html,body{width:1200px;height:3390px;overflow:hidden}
body{position:relative;background:var(--white);font-family:"Open Sans",Arial,sans-serif;color:var(--text)}
.abs{position:absolute}

/* header */
.site-header{left:0;top:0;width:1200px;height:130px;background:var(--dark);color:var(--white)}
.brand{left:160px;top:30px;display:flex;align-items:center;gap:10px;font-family:"Montserrat",Arial,sans-serif;font-weight:700;font-size:15px;letter-spacing:2px;color:var(--white)}
.brand-mark{width:22px;height:22px;background:var(--orange)}
.contact-line{top:16px;display:flex;align-items:center;gap:14px;font-family:"Montserrat",Arial,sans-serif;font-size:14px;line-height:22px}
.contact-line b{font-weight:600;display:block}
.call{left:680px}
.mail{left:880px}
.main-nav{left:468px;top:90px;display:flex;gap:38px;font-family:"Montserrat",Arial,sans-serif;font-weight:500;font-size:16px}
.social-top{left:968px;top:94px;display:flex;gap:22px}
.social-top span{width:12px;height:12px;border-radius:50%;background:var(--white)}

/* hero */
.hero{left:0;top:130px;width:1200px;height:605px;background:linear-gradient(170deg,#27386e 0%,#4a5b8f 35%,#8a7a86 62%,#d09a5c 85%,#a9683a 100%)}
.hero-box{left:270px;top:85px;width:662px;height:360px;border:3px solid var(--orange);background:rgba(70,70,80,.62);text-align:center;color:var(--white)}
.hero-box h1{margin-top:70px;font-family:"Montserrat",Arial,sans-serif;font-weight:600;font-size:52px;letter-spacing:1px}
.hero-box p{margin:12px auto 0;width:520px;font-size:17px;line-height:30px}
.btn{display:inline-flex;align-items:center;justify-content:center;gap:10px;background:var(--orange);color:var(--white);font-family:"Montserrat",Arial,sans-serif;font-weight:600;font-size:16px;height:48px;box-shadow:0 3px 6px rgba(0,0,0,.25)}
.hero-box .btn{margin-top:18px;width:180px}

.band{left:0;width:1200px}
.grey{background:var(--grey)}

/* section titles */
.section-title{left:0;width:1200px;text-align:center;height:60px}
.section-title .ghost{position:absolute;left:0;width:1200px;top:-14px;font-family:"Montserrat",Arial,sans-serif;font-weight:600;font-size:48px;color:var(--orange-soft);letter-spacing:2px}
.section-title h2{position:relative;font-family:"Montserrat",Arial,sans-serif;font-weight:700;font-size:32px;color:var(--orange)}
.copy{left:130px;width:940px;text-align:center;font-size:15.5px;line-height:31px;color:var(--text)}

.values-title{left:0;width:1200px;top:1036px;text-align:center;font-family:"Montserrat",Arial,sans-serif;font-weight:700;font-size:20px;color:var(--ink)}
.value-card{top:1080px;width:308px;height:176px;box-shadow:0 3px 6px rgba(0,0,0,.2)}
.value-card .photo{width:100%;height:140px}
.value-card .label{height:36px;background:var(--orange);color:var(--white);text-align:center;line-height:36px;font-family:"Montserrat",Arial,sans-serif;font-size:16px}

.icon-art{height:158px;background:linear-gradient(90deg,#f3d6ca,#f6e2d9)}

/* form */
.field{height:44px;background:var(--white);border-bottom:3px solid var(--field-line);box-shadow:0 1px 3px rgba(0,0,0,.12);font-size:12px;padding:12px 18px;color:#444;display:flex;gap:8px;align-items:flex-start}
.field i{width:9px;height:9px;margin-top:3px;background:#555;border-radius:2px}
.message{height:150px}

.site-footer{left:0;top:3300px;width:1200px;height:90px;background:var(--dark);color:var(--white);text-align:center}
.foot-social{display:flex;justify-content:center;gap:8px;margin-top:19px}
.foot-social span{width:30px;height:30px;border-radius:50%;border:2px solid var(--white)}
.site-footer p{margin-top:9px;font-family:"Montserrat",Arial,sans-serif;font-size:14px}
</style>
</head>
<body>

<header class="abs site-header">
  <div class="abs brand"><span class="brand-mark"></span>KEEL INDUSTRIES</div>
  <div class="abs contact-line call">
    <svg width="40" height="40" viewBox="0 0 40 40"><circle cx="20" cy="20" r="18" fill="none" stroke="#fff" stroke-width="2.5"/><path d="M14 11c2 0 3 4 3 5s-2 2-2 3c1 3 3 5 6 6 1 0 2-2 3-2s5 1 5 3-2 4-4 4c-7 0-14-7-14-14 0-2 1-5 3-5z" fill="#fff"/></svg>
    <div><b>Call us:</b>555 014-2290</div>
  </div>
  <div class="abs contact-line mail">
    <svg width="46" height="32" viewBox="0 0 46 32"><rect x="2" y="2" width="42" height="28" fill="none" stroke="#fff" stroke-width="2.5"/><path d="M2 2l21 16L44 2" fill="none" stroke="#fff" stroke-width="2.5"/></svg>
    <div><b>Mail us:</b>info@keel-works.com</div>
  </div>
  <nav class="abs main-nav"><span>HOME</span><span>MACHINING</span><span>SOURCING</span><span>CONTACT</span></nav>
  <div class="abs social-top"><span></span><span></span><span></span></div>
</header>

<section class="abs hero" role="img" aria-label="Construction cranes against a sunset sky">
  <div class="abs hero-box">
    <h1>KEEL INDUSTRIES</h1>
    <p>Sed ut perspiciatis unde omnis iste natus error sit voluptatem accusantium doloremque laudantium</p>
    <span class="btn">
      <svg width="16" height="16" viewBox="0 0 16 16"><path d="M15 1L1 7l6 2 2 6z" fill="#fff"/></svg>CONTACT US</span>
  </div>
</section>

<svg class="abs" style="left:0;top:640px" width="1200" height="100" viewBox="0 0 1200 100">
  <polygon points="0,95 600,48 1200,0 1200,100 0,100" fill="#e9e9e9"/>
  <polygon points="600,48 1200,0 1200,95" fill="#e8501c"/>
</svg>

<section class="abs band grey" style="top:735px;height:615px"></section>
<div class="abs section-title" style="top:835px"><span class="ghost">ABOUT US</span><h2>Quality Policy</h2></div>
<p class="abs copy" style="top:885px">We are committed to consistently exceeding customer expectations by providing products, services and sourcing solutions of the highest standard of quality. With our streamlined processes our method is efficient, provides value and ensures on time delivery. Our success is based on continuously improving the efficiencies and effectiveness of our products, processes, and quality management systems.</p>
<h3 class="abs values-title">CORE VALUES</h3>
<div class="abs value-card" style="left:110px"><div class="photo" role="img" aria-label="Team working together around a table" style="background:linear-gradient(135deg,#6a5a4c,#a08e78)"></div><div class="label">Teamwork</div></div>
<div class="abs value-card" style="left:447px"><div class="photo" role="img" aria-label="Site workers in hard hats and safety vests" style="background:linear-gradient(135deg,#7ea5d2,#b9c86a)"></div><div class="label">Respect</div></div>
<div class="abs value-card" style="left:782px"><div class="photo" role="img" aria-label="Two engineers in hard hats talking on site" style="background:linear-gradient(135deg,#4d5663,#c49b47)"></div><div class="label">Gratitude</div></div>

<div class="abs section-title" style="top:1463px"><span class="ghost">MACHINING</span><h2>MACHINING</h2></div>
<div class="abs icon-art" style="left:305px;top:1537px;width:600px" role="img" aria-label="Line illustrations of a blueprint, a robotic arm and a shipping box"></div>
<p class="abs copy" style="top:1725px">Keel Industries brings their machining knowledge to the table every day working closely with our customers to put value into each part we produce. Working as a strategic partner, Keel Industries is able to deliver precision machined components with the highest quality, on time, and at the most cost effective price.</p>
<span class="abs btn" style="left:510px;top:1842px;width:180px">
  <svg width="18" height="14" viewBox="0 0 18 14"><circle cx="6" cy="8" r="4" fill="none" stroke="#fff" stroke-width="2.5"/><circle cx="14" cy="4" r="2.5" fill="none" stroke="#fff" stroke-width="2"/></svg>READ MORE</span>

<svg class="abs" style="left:0;top:1970px" width="1200" height="112" viewBox="0 0 1200 112">
  <polygon points="0,40 600,40 1200,95 1200,112 0,112" fill="#e9e9e9"/>
  <polygon points="0,0 600,40 0,95" fill="#e8501c"/>
</svg>
<section class="abs band grey" style="top:2080px;height:612px"></section>

<div class="abs section-title" style="top:2152px"><span class="ghost">SOURCING</span><h2>SOURCING</h2></div>
<div class="abs icon-art" style="left:295px;top:2226px;width:610px;height:148px" role="img" aria-label="Line illustrations of a strategy board, a checklist and a delivery truck"></div>
<p class="abs copy" style="top:2403px">Over the years we identified the need to provide one stop services to purchasing departments. We have built an extensive network of hard to find products, machining specialists and leveraging open machine time to provide the most economical alternatives to our customers. We have developed a specialized method to supply our customers with the benefits they desire.</p>
<span class="abs btn" style="left:510px;top:2560px;width:180px">
  <svg width="18" height="14" viewBox="0 0 18 14"><circle cx="6" cy="8" r="4" fill="none" stroke="#fff" stroke-width="2.5"/><circle cx="14" cy="4" r="2.5" fill="none" stroke="#fff" stroke-width="2"/></svg>READ MORE</span>

<svg class="abs" style="left:0;top:2688px" width="1200" height="96" viewBox="0 0 1200 96">
  <polygon points="0,0 1200,0 1200,10 600,48 0,92" fill="#e9e9e9"/>
  <polygon points="600,48 1200,0 1200,92" fill="#e8501c"/>
</svg>

<div class="abs section-title" style="top:2866px"><span class="ghost">CONTACT US</span><h2>CONTACT US</h2></div>
<div class="abs field" style="left:163px;top:2950px;width:429px"><i></i>First Name</div>
<div class="abs field" style="left:610px;top:2950px;width:430px"><i></i>Last Name</div>
<div class="abs field" style="left:163px;top:3004px;width:429px"><i></i>Address</div>
<div class="abs field" style="left:163px;top:3058px;width:429px"><i></i>Email Address</div>
<div class="abs field" style="left:163px;top:3112px;width:429px"><i></i>Phone Number</div>
<div class="abs field message" style="left:610px;top:3004px;width:430px"><i></i>Message :</div>
<span class="abs btn" style="left:510px;top:3164px;width:180px">SUBMIT</span>

<footer class="abs site-footer">
  <div class="foot-social"><span></span><span></span><span></span><span></span></div>
  <p>© 2019 Company Name &nbsp;All right reserved</p>
</footer>

</body>
</html>
```